Car transport business

We need a new business card design. Attached is our old card sample. I would just like to adjust the logo colors (blue and red) to be brighter. I changed my name to the brighter red and the word dispatcher to a brighter blue as an example. But you can adjust those colors further. And then perhaps you can use the same colors for the card design but use your imagination.

As a suggestion so the card stands out I would like to add a clip art of car carrier truck. Attached are examples of that as well

```html
<!DOCTYPE html>
<html lang="en">
<head>
<meta charset="UTF-8">
<title>Keystone Haul — Business Card</title>
<link href="https://fonts.googleapis.com/css2?family=Montserrat:wght@400;500;600;700&display=swap" rel="stylesheet">
<style>
  :root {
    --page-bg: #e4e4e4;
    --card-white: #ffffff;
    --brand-blue: #165a86;
    --brand-red: #c11f2c;
    --on-blue: #ffffff;
  }
  * { margin: 0; padding: 0; box-sizing: border-box; }
  html, body { width: 1200px; height: 1200px; overflow: hidden; }
  body {
    background: var(--page-bg);
    font-family: "Montserrat", Arial, sans-serif;
    position: relative;
  }
  .card {
    position: absolute;
    left: 200px;
    width: 759px;
    height: 434px;
  }
  .card--front { top: 108px; background: var(--card-white); }
  .card--back { top: 618px; background: var(--brand-blue); }

  .brand { position: absolute; display: flex; flex-direction: column; }
  .brand__row { display: flex; align-items: center; gap: 10px; }
  .brand__dot { border-radius: 50%; flex: none; }
  .brand__name {
    font-weight: 700;
    text-transform: uppercase;
    white-space: nowrap;
    line-height: 1;
  }
  .brand__slogan {
    text-transform: uppercase;
    font-weight: 500;
    white-space: nowrap;
  }

  .card--front .brand { left: 58px; top: 182px; }
  .card--front .brand__dot { width: 26px; height: 26px; background: var(--brand-red); }
  .card--front .brand__name { font-size: 30px; color: var(--brand-blue); letter-spacing: 0.5px; }
  .card--front .brand__slogan {
    font-size: 9.5px; letter-spacing: 1.9px; color: var(--brand-blue);
    margin-top: 5px; margin-left: 36px;
  }

  .divider {
    position: absolute; left: 392px; top: 148px;
    width: 1.5px; height: 139px; background: var(--brand-red);
  }

  .contact { position: absolute; left: 426px; top: 142px; }
  .contact__name {
    font-size: 40px; font-weight: 600; color: var(--brand-red);
    line-height: 1; letter-spacing: 0.3px;
  }
  .contact__role {
    font-size: 19px; color: var(--brand-blue); text-transform: uppercase;
    margin-top: 6px; letter-spacing: 0.3px;
  }
  .contact__list { list-style: none; margin-top: 18px; }
  .contact__item {
    display: flex; align-items: center; gap: 6px;
    font-size: 19px; color: var(--brand-blue); line-height: 25px;
  }
  .contact__icon { width: 15px; height: 15px; flex: none; }

  .card--back .brand { left: 130px; top: 206px; }
  .card--back .brand__dot { width: 46px; height: 46px; background: var(--on-blue); }
  .card--back .brand__name { font-size: 46px; color: var(--on-blue); letter-spacing: 1px; }
  .card--back .brand__slogan {
    font-size: 14.5px; letter-spacing: 3.2px; color: var(--on-blue);
    margin-top: 6px; margin-left: 56px;
  }
</style>
</head>
<body>
  <section class="card card--front">
    <div class="brand">
      <div class="brand__row">
        <span class="brand__dot"></span>
        <span class="brand__name">Keystone Haul</span>
      </div>
      <span class="brand__slogan">Trusted Car Shipping Specialists</span>
    </div>

    <div class="divider"></div>

    <div class="contact">
      <h1 class="contact__name">OMAR VELL</h1>
      <p class="contact__role">Dispatcher</p>
      <ul class="contact__list">
        <li class="contact__item">
          <svg class="contact__icon" viewBox="0 0 16 16" aria-hidden="true">
            <path d="M4 1.5l2 3-1.3 1.4c.8 2 2.3 3.6 4.2 4.6L10.3 9l3 1.8-.8 2.6c-.3.8-1.2 1.1-2 .8C6 12.6 3 9.4 1.8 5c-.2-.8.2-1.6 1-1.9z" fill="var(--brand-red)"/>
          </svg>
          555-014-2786
        </li>
        <li class="contact__item">
          <svg class="contact__icon" viewBox="0 0 16 16" aria-hidden="true">
            <rect x="4" y="1.5" width="8" height="4" fill="var(--brand-red)"/>
            <rect x="1" y="5.5" width="14" height="6" rx="1" fill="var(--brand-red)"/>
            <rect x="4" y="10" width="8" height="4.5" fill="var(--brand-red)"/>
            <rect x="5" y="11" width="6" height="1" fill="#fff"/>
          </svg>
          555-014-3390
        </li>
        <li class="contact__item">
          <svg class="contact__icon" viewBox="0 0 16 16" aria-hidden="true">
            <rect x="1.5" y="3.5" width="13" height="9" rx="1" fill="none" stroke="var(--brand-red)" stroke-width="1.4"/>
            <path d="M2 4.2l6 4.6 6-4.6" fill="none" stroke="var(--brand-red)" stroke-width="1.4"/>
          </svg>
          keystonehaul@mailbox.com
        </li>
      </ul>
    </div>
  </section>

  <section class="card card--back">
    <div class="brand">
      <div class="brand__row">
        <span class="brand__dot"></span>
        <span class="brand__name">Keystone Haul</span>
      </div>
      <span class="brand__slogan">Trusted Car Shipping Specialists</span>
    </div>
  </section>
</body>
</html>
```